All-Natural Head Lice Removal company

I need a business card with my pre-existing logo. We are a new company located in Portland Oregon that goes into peoples homes to help with head lice removal. My products and approach are all- natural and also will be around children.On my current logo we used Teal Bl and the color Green. I am open to new ideas just want it simple and creative

Target Market(s)

my biggest market is families of school aged children

Industry/Entity Type

Business

Contact Information for Business Card

see upload for details from previous business card

Font styles to use
Serif

Colors
33a6d7
9bcb3b
f37122

Requirements
Must have
• Basic information/ logo put into a creative format that is catching to the eye
Nice to have
• creative

```html
<!DOCTYPE html>
<html lang="en">
<head>
<meta charset="utf-8">
<title>Nitwise Business Card</title>
<link href="https://fonts.googleapis.com/css2?family=Ubuntu:wght@400;500;700&display=swap" rel="stylesheet">
<style>
  :root {
    --bg: #ece8e1;
    --card-white: #ffffff;
    --card-grey: #e9e9e9;
    --leaf: #6cb33f;
    --leaf-light: #7cc24a;
    --leaf-dark: #5a9c33;
    --teal: #33a6d7;
    --ink: #1f1f1f;
    --rule: #3a3a3a;
  }
  * { margin: 0; padding: 0; box-sizing: border-box; }
  html, body { width: 1200px; height: 1023px; overflow: hidden; }
  body {
    background: var(--bg);
    font-family: "Ubuntu", sans-serif;
    color: var(--ink);
    position: relative;
  }
  .card {
    position: absolute;
    width: 525px;
    height: 300px;
    border-radius: 22px;
    overflow: hidden;
    box-shadow: 0 10px 24px rgba(0,0,0,0.18);
  }
  /* Front */
  .card-front {
    left: 337px;
    top: 150px;
    background: linear-gradient(135deg, var(--card-white) 0%, var(--card-grey) 100%);
  }
  .front-wave { position: absolute; left: 0; top: 0; width: 525px; height: 300px; }
  .brand {
    position: absolute;
    left: 26px;
    top: 120px;
    display: flex;
    align-items: center;
    gap: 10px;
  }
  .brand-dot {
    width: 34px; height: 34px; border-radius: 50%;
    background: var(--leaf);
  }
  .brand-name {
    font-weight: 700;
    font-size: 30px;
    color: var(--ink);
  }
  .tagline {
    position: absolute;
    left: 200px;
    top: 34px;
    width: 300px;
    font-weight: 700;
    font-size: 19px;
    line-height: 1.25;
  }
  .person {
    position: absolute;
    right: 34px;
    top: 118px;
    text-align: right;
  }
  .person-name { color: var(--leaf); font-weight: 700; font-size: 19px; }
  .person-role { font-weight: 700; font-size: 11px; margin-top: 4px; color: #444; }
  .divider {
    position: absolute;
    left: 200px; right: 34px; top: 166px;
    height: 1px; background: var(--rule);
  }
  .contact {
    position: absolute;
    left: 200px;
    top: 182px;
    font-size: 13px;
    line-height: 1.5;
    list-style: none;
  }
  .contact-label { color: var(--leaf); font-weight: 700; margin-right: 4px; }
  /* Back */
  .card-back {
    left: 337px;
    top: 560px;
    background: linear-gradient(160deg, var(--leaf-light) 0%, var(--leaf) 60%, var(--leaf-dark) 100%);
  }
  .back-brand {
    position: absolute;
    left: 0; right: 0; top: 62px;
    display: flex;
    justify-content: center;
    align-items: center;
    gap: 12px;
  }
  .back-brand .brand-dot { background: var(--ink); width: 40px; height: 40px; }
  .back-brand .brand-name { font-size: 40px; }
  .back-copy {
    position: absolute;
    left: 0; right: 0; top: 170px;
    text-align: center;
    font-size: 15px;
    line-height: 1.45;
    color: var(--ink);
  }
  .web-accent { color: var(--teal); }
</style>
</head>
<body>
  <section class="card card-front" aria-label="Business card front">
    <svg class="front-wave" viewBox="0 0 525 300" aria-hidden="true">
      <path d="M0 190 C 70 215, 130 250, 175 300 L 0 300 Z" fill="var(--teal)"/>
      <path d="M0 200 C 70 225, 125 258, 165 300 L 0 300 Z" fill="var(--leaf)"/>
    </svg>
    <div class="brand">
      <span class="brand-dot"></span>
      <span class="brand-name">Nitwise</span>
    </div>
    <h1 class="tagline">All Natural In-Home Lice Removal Services</h1>
    <div class="person">
      <p class="person-name">Marla Quinn</p>
      <p class="person-role">Owner</p>
    </div>
    <div class="divider"></div>
    <ul class="contact">
      <li><span class="contact-label">P :</span>1-555-014-NITS (6487)</li>
      <li><span class="contact-label">E :</span>marla@nitwisecare.com</li>
      <li><span class="contact-label">W :</span>www.<span class="web-accent">nitwisecare</span>.com</li>
    </ul>
  </section>

  <section class="card card-back" aria-label="Business card back">
    <div class="back-brand">
      <span class="brand-dot"></span>
      <span class="brand-name">Nitwise</span>
    </div>
    <div class="back-copy">
      <p>Try Nitwise Today and Be Lice Free Tomorrow!</p>
      <p>All Natural In-Home Lice Removal Service</p>
      <p>www.<span class="web-accent">nitwisecare</span>.com</p>
    </div>
  </section>
</body>
</html>
```